Vernac Law Business cards and stationary design project

We are looking for a stationary design for business cards (double sided), 8x10, 5x7, and legal and standard envelopes.

We would like the design to match the logo that we have already.
Color palate preferred is Teal, White, grey and any others that will look good for a professional law firm.

We would like this statement: "RELATIONSHIPS. RESPECT. RESULT" to be on the back of the business cards and maybe on the stationary if it looks good.

Please see link to website for more information: www.vernac-law.example

Target Market(s)

Potential clients that need Attorney services.

Industry/Entity Type

Law Firm

Contact Information for Business Card

We would like the front and back to be two different colors. Current business cards are teal front, grey back and are a vertical design. We are open to options with colors.

Font styles to use
Serif

Colors
33a6d7
33b8a4
b9b9b9
5c5c5c

Requirements
Must have
• Logo supplied needs to go on the card and stationary.
• Match website color palate, www.vernac-law.example
• Be professional and not too wordy.
• Criminal Law, Civil Litigation, Personal Injury, Restraining Orders need to be on the card.
Nice to have
• RELATIONSHIPS. RESPECT. RESULTS. on the back of the card.
Should not have
• Not be too busy/wordy or too flashy.

```html
<!DOCTYPE html>
<html lang="en">
<head>
<meta charset="utf-8">
<title>Vernac Law — Business Card</title>
<link rel="stylesheet" href="https://fonts.googleapis.com/css2?family=Cinzel:wght@400;600&family=EB+Garamond:wght@400;500&display=swap">
<style>
  :root {
    --page: #ece9e4;
    --teal: #0f8a99;
    --grey: #6d6d6d;
    --white: #ffffff;
    --soft-white: rgba(255,255,255,0.85);
    --shadow: rgba(0,0,0,0.18);
  }
  * { box-sizing: border-box; margin: 0; padding: 0; }
  html, body { width: 1200px; height: 950px; overflow: hidden; }
  body {
    background: var(--page);
    position: relative;
    font-family: "EB Garamond", Georgia, serif;
    color: var(--white);
  }
  .card {
    position: absolute;
    top: 125px;
    width: 400px;
    height: 700px;
    box-shadow: 0 8px 24px var(--shadow);
  }
  .card--front { left: 160px; background: var(--teal); }
  .card--back { left: 640px; background: var(--grey); }
  .card__frame {
    position: absolute;
    inset: 18px;
    border: 2px solid var(--white);
  }

  /* Firm name in place of the mark */
  .firm-mark {
    position: absolute;
    left: 0; right: 0;
    display: flex;
    flex-direction: column;
    align-items: center;
    gap: 12px;
    font-family: "EB Garamond", Georgia, serif;
    font-weight: 400;
    color: var(--white);
  }
  .firm-mark__square {
    background: var(--white);
  }
  .card--front .firm-mark { top: 52px; }
  .card--front .firm-mark__square { width: 40px; height: 40px; }
  .card--front .firm-mark__name { font-size: 30px; letter-spacing: 2px; }
  .card--back .firm-mark { top: 95px; gap: 16px; }
  .card--back .firm-mark__square { width: 70px; height: 70px; }
  .card--back .firm-mark__name { font-size: 36px; letter-spacing: 2px; }

  /* Front */
  .person {
    position: absolute;
    top: 440px; left: 0; right: 0;
    text-align: center;
  }
  .person__name {
    font-family: "Cinzel", "Times New Roman", serif;
    font-weight: 600;
    font-size: 30px;
    letter-spacing: 1.5px;
  }
  .person__title {
    font-family: "Cinzel", "Times New Roman", serif;
    font-size: 15px;
    letter-spacing: 2px;
    margin-top: 2px;
  }
  .divider {
    width: 240px; margin: 14px auto 0;
    border-top: 2px dotted var(--soft-white);
  }
  .contact {
    list-style: none;
    position: absolute;
    top: 548px; left: 62px;
    font-size: 19px;
    line-height: 1.3;
  }
  .contact li { display: flex; align-items: center; gap: 10px; }
  .contact svg { width: 16px; height: 16px; flex: none; }

  /* Back */
  .motto {
    position: absolute;
    top: 460px; left: 70px;
    font-size: 20px;
    letter-spacing: 1.5px;
    line-height: 1.15;
    text-transform: uppercase;
  }
  .back-divider {
    position: absolute;
    top: 520px; left: 60px; width: 280px;
    border-top: 2px dotted var(--soft-white);
  }
  .practice {
    list-style: none;
    position: absolute;
    top: 545px; right: 58px;
    text-align: right;
    font-size: 19px;
    line-height: 1.2;
  }
</style>
</head>
<body>
  <section class="card card--front" aria-label="Business card front">
    <div class="card__frame"></div>
    <div class="firm-mark">
      <span class="firm-mark__square"></span>
      <span class="firm-mark__name">Vernac Law</span>
    </div>
    <div class="person">
      <div class="person__name">Mara Ellison</div>
      <div class="person__title">Trial Lawyer</div>
      <div class="divider"></div>
    </div>
    <ul class="contact">
      <li>
        <svg viewBox="0 0 16 16" aria-hidden="true"><path fill="#fff" d="M3.6 1.5l2.3 2.6-1.2 1.6c.9 2 2.6 3.7 4.6 4.6l1.6-1.2 2.6 2.3-1.4 2.1C7 13.3 2.7 9 1.5 2.9z"/></svg>
        (555) 014-2280
      </li>
      <li>
        <svg viewBox="0 0 16 16" aria-hidden="true"><rect x="1.5" y="3.5" width="13" height="9" fill="#fff"/><path d="M1.5 3.5l6.5 5 6.5-5" fill="none" stroke="#0f8a99" stroke-width="1.2"/></svg>
        mara@vernac-law.example
      </li>
      <li>
        <svg viewBox="0 0 16 16" aria-hidden="true"><circle cx="8" cy="8" r="6.5" fill="#fff"/><path d="M1.5 8h13M8 1.5c-3 3.5-3 9.5 0 13M8 1.5c3 3.5 3 9.5 0 13" fill="none" stroke="#0f8a99" stroke-width="1"/></svg>
        www.vernac-law.example
      </li>
    </ul>
  </section>

  <section class="card card--back" aria-label="Business card back">
    <div class="card__frame"></div>
    <div class="firm-mark">
      <span class="firm-mark__square"></span>
      <span class="firm-mark__name">Vernac Law</span>
    </div>
    <div class="motto">Relationships<br>Respect. Results</div>
    <div class="back-divider"></div>
    <ul class="practice">
      <li>Criminal Law</li>
      <li>Civil Litigation/Personal Injury</li>
      <li>Restraining</li>
    </ul>
  </section>
</body>
</html>
```